Gutschein-Design für Verkauf von Online-Schmuckstücken
Zielgruppe
Wir verkaufen Online Schmuckstücke!
www.silberfaden-shop.de
Aufgabenstellung
Wir haben eine schwarze Schachtel erstellt und da drinne wird eine Geschenkgutschein sein:
Es soll sehr schlicht sein und schwarzen Hintergrund haben.
Vorderseite nur unser LOGO.
Rückseite:
Betrag: _________
Gültig Bis: _________
Code: __________
Und unten klein gedruckt steht:
Diese Karte ist gültig nur auf der online shop seite www.silberfaden-shop.de und in unserer offizielen Stores. Dieses Karte ist nicht gültig bei rabatierte Produkten und man kann nicht mit dieser karte einen Gutscheinkarte kaufen.
Der Design soll sehr schlicht und dezenz sein.

```html
<!DOCTYPE html>
<html lang="de">
<head>
<meta charset="utf-8">
<title>Silberfaden Geschenkgutschein</title>
<link href="https://fonts.googleapis.com/css2?family=Great+Vibes&family=Allura&family=Lato:wght@400&display=swap" rel="stylesheet">
<style>
  :root {
    --ink: #111111;
    --paper: #ffffff;
    --frame-line: #ffffff;
    --blush-light: #fcf1e8;
    --blush: #f5b2c8;
    --blush-pale: #f9eef3;
    --fine-print: #c98aa0;
  }
  html, body {
    margin: 0;
    padding: 0;
    width: 1200px;
    height: 851px;
    overflow: hidden;
    background: var(--paper);
  }
  .voucher {
    position: relative;
    width: 1200px;
    height: 851px;
    overflow: hidden;
  }

  /* Front side */
  .front {
    position: absolute;
    left: 0;
    top: 0;
    width: 590px;
    height: 851px;
    background: var(--paper);
    overflow: hidden;
  }
  .brand-dot {
    position: absolute;
    left: 103px;
    top: 326px;
    width: 232px;
    height: 232px;
    border-radius: 50%;
    background: var(--ink);
  }
  .brand-name {
    position: absolute;
    left: 462px;
    top: 430px;
    transform: translate(-50%, -50%) rotate(-90deg);
    margin: 0;
    font-family: "Great Vibes", cursive;
    font-weight: 400;
    font-size: 168px;
    letter-spacing: 6px;
    line-height: 1;
    color: var(--ink);
    white-space: nowrap;
  }

  /* Back side */
  .back {
    position: absolute;
    left: 590px;
    top: 0;
    width: 610px;
    height: 851px;
  }
  .lace-border {
    position: absolute;
    inset: 0;
    background: var(--ink);
  }
  .inner-frame {
    position: absolute;
    left: 55px;
    top: 20px;
    width: 501px;
    height: 803px;
    border: 1.5px solid var(--frame-line);
  }
  .blush-panel {
    position: absolute;
    left: 61px;
    top: 26px;
    width: 491px;
    height: 792px;
    background:
      radial-gradient(ellipse at 18% 22%, var(--blush-light) 0%, rgba(252,241,232,0) 55%),
      radial-gradient(ellipse at 90% 95%, var(--blush-pale) 0%, rgba(249,238,243,0) 50%),
      linear-gradient(160deg, var(--blush-light) 0%, #f6c6d4 45%, var(--blush) 100%);
  }

  .fields {
    position: absolute;
    left: 655px;
    top: 300px;
    width: 490px;
    height: 420px;
    transform: rotate(-90deg);
    transform-origin: 245px 210px;
  }
  .field {
    position: absolute;
    right: 0;
    height: 90px;
    display: flex;
    align-items: flex-end;
    justify-content: flex-end;
    font-family: "Allura", cursive;
    font-size: 74px;
    line-height: 0.9;
    color: var(--ink);
    white-space: nowrap;
  }
  .field-betrag { top: -5px; }
  .field-gueltig { top: 141px; }
  .field-code { top: 310px; }
  .field-line {
    display: inline-block;
    width: 198px;
    height: 0;
    border-bottom: 2px solid var(--ink);
    margin-left: 4px;
    margin-bottom: 6px;
  }

  .fine-print {
    position: absolute;
    left: 1187px;
    top: 412px;
    width: 440px;
    transform: translate(-50%, -50%) rotate(-90deg);
    margin: 0;
    font-family: "Lato", sans-serif;
    font-size: 5.6px;
    line-height: 1.3;
    color: var(--fine-print);
    text-align: center;
  }
</style>
</head>
<body>
<main class="voucher">
  <section class="front">
    <div class="brand-dot"></div>
    <h1 class="brand-name">Silberfaden</h1>
  </section>

  <section class="back">
    <div class="lace-border" role="img" aria-label="Schwarze ornamentale Spitzenbordüre"></div>
    <div class="inner-frame"></div>
    <div class="blush-panel"></div>
  </section>

  <div class="fields">
    <div class="field field-betrag">Betrag:<span class="field-line"></span></div>
    <div class="field field-gueltig">Gültig Bis:<span class="field-line"></span></div>
    <div class="field field-code">Code:<span class="field-line"></span></div>
  </div>

  <p class="fine-print">Diese Karte ist nur auf der Online Shop Seite www.silberfaden-shop.de und in unseren offiziellen Stores gültig.<br>Diese Karte ist bei rabattierten Produkten nicht gültig. Man kann mit dieser Karte keine Gutscheinkarte kaufen.</p>
</main>
</body>
</html>
```